Stonebridge Building and Projects business cards

A business card with watermark background (construction work)

Company logo attached

Home improvement projects
House renovations
Bathroom and kitchen renovations
House extensions
New builds and granny flats

Director Omar Haddani
(Phone number)
omar@sbpbuilding.com.au
(Instagram logo) sbp_building

```html
<!DOCTYPE html>
<html lang="en">
<head>
<meta charset="utf-8">
<title>Stonebridge Building and Projects – Business Cards</title>
<link rel="stylesheet" href="https://fonts.googleapis.com/css2?family=Montserrat:wght@400;600;700&display=swap">
<style>
  :root {
    --brand-blue: #2f76b8;
    --ink-dark: #2a2a2a;
    --paper: #ffffff;
    --backdrop: #e9ebee;
  }
  * { box-sizing: border-box; margin: 0; padding: 0; }
  html, body { width: 1200px; height: 1015px; overflow: hidden; }
  body {
    background: var(--backdrop);
    font-family: "Montserrat", Arial, sans-serif;
    position: relative;
  }
  .card {
    position: absolute;
    left: 232px;
    width: 735px;
    height: 420px;
    background: var(--brand-blue);
    overflow: hidden;
    box-shadow: 0 6px 18px rgba(0,0,0,.18);
  }
  .card--services { top: 58px; }
  .card--contact { top: 537px; }
  .card-shape { position: absolute; inset: 0; }

  .brand {
    position: absolute;
    display: flex;
    align-items: center;
    gap: 12px;
    color: var(--brand-blue);
  }
  .brand-mark {
    width: 20px; height: 20px;
    background: var(--brand-blue);
    flex: none;
  }
  .brand-name {
    font-weight: 700;
    font-size: 20px;
    line-height: 1.25;
  }
  .brand-tagline {
    display: block;
    margin-top: 8px;
    padding-top: 6px;
    border-top: 2px solid var(--brand-blue);
    font-weight: 700;
    font-size: 13px;
  }
  .card--services .brand { left: 44px; top: 150px; width: 290px; }
  .card--contact .brand { left: 420px; top: 140px; width: 280px; }

  .service-list {
    position: absolute;
    right: 36px;
    top: 38px;
    list-style: none;
    text-align: right;
    color: var(--paper);
    font-size: 15px;
    line-height: 30px;
  }
  .service-list li::after {
    content: "";
    display: inline-block;
    width: 8px; height: 8px;
    margin-left: 8px;
    border-radius: 50%;
    background: var(--paper);
    vertical-align: middle;
  }

  .person { position: absolute; left: 48px; top: 64px; color: var(--paper); }
  .person-name { font-weight: 700; font-size: 26px; }
  .person-role { font-size: 17px; margin-top: 2px; }

  .contact-list {
    position: absolute;
    left: 48px;
    top: 200px;
    list-style: none;
    color: var(--paper);
    font-size: 16px;
    line-height: 28px;
  }
  .contact-list li { display: flex; align-items: center; gap: 10px; }
  .contact-list .social { margin-bottom: 48px; font-size: 17px; }
  .contact-icon { width: 16px; height: 16px; flex: none; }
</style>
</head>
<body>

<section class="card card--services" aria-label="Business card, services side">
  <svg class="card-shape" viewBox="0 0 735 420" aria-hidden="true">
    <circle cx="187" cy="220" r="229" fill="var(--ink-dark)"/>
    <circle cx="173" cy="220" r="227" fill="var(--paper)"/>
  </svg>
  <div class="brand">
    <span class="brand-mark"></span>
    <div class="brand-name">Stonebridge Building and Projects
      <span class="brand-tagline">Built on solid ground</span>
    </div>
  </div>
  <ul class="service-list">
    <li>Home improvement projects</li>
    <li>House renovations</li>
    <li>House extensions</li>
    <li>New builds and granny flats</li>
    <li>Bathroom and kitchen renovations</li>
  </ul>
</section>

<section class="card card--contact" aria-label="Business card, contact side">
  <svg class="card-shape" viewBox="0 0 735 420" aria-hidden="true">
    <circle cx="548" cy="190" r="229" fill="var(--ink-dark)"/>
    <circle cx="562" cy="190" r="227" fill="var(--paper)"/>
  </svg>
  <div class="person">
    <div class="person-name">Omar Haddani</div>
    <div class="person-role">Director</div>
  </div>
  <ul class="contact-list">
    <li class="social">
      <svg class="contact-icon" viewBox="0 0 16 16" aria-hidden="true"><rect x="1" y="1" width="14" height="14" rx="3" fill="var(--paper)"/></svg>
      sbp_building
    </li>
    <li>
      <svg class="contact-icon" viewBox="0 0 16 16" aria-hidden="true"><path d="M3 1l3 3-1.5 2a9 9 0 0 0 5.5 5.5L12 10l3 3-2 2C7 15 1 9 1 3z" fill="var(--paper)"/></svg>
      044-555 010 321
    </li>
    <li>
      <svg class="contact-icon" viewBox="0 0 16 16" aria-hidden="true"><rect x="1" y="3" width="14" height="10" fill="none" stroke="var(--paper)" stroke-width="1.6"/><path d="M1 3l7 6 7-6" fill="none" stroke="var(--paper)" stroke-width="1.6"/></svg>
      omar@sbpbuilding.com.au
    </li>
    <li>
      <svg class="contact-icon" viewBox="0 0 16 16" aria-hidden="true"><circle cx="8" cy="8" r="6.5" fill="none" stroke="var(--paper)" stroke-width="1.4"/><ellipse cx="8" cy="8" rx="3" ry="6.5" fill="none" stroke="var(--paper)" stroke-width="1.2"/><path d="M1.5 8h13" stroke="var(--paper)" stroke-width="1.2"/></svg>
      www.sbpbuilding.com.au
    </li>
  </ul>
  <div class="brand">
    <span class="brand-mark"></span>
    <div class="brand-name">Stonebridge Building and Projects
      <span class="brand-tagline">Built on solid ground</span>
    </div>
  </div>
</section>

</body>
</html>
```